Business Card Design

Want something very unique. No business, just personal. The image I submitted is for inspiration only.

Target Market(s)

friends and new acquaintances

Industry/Entity Type

Business

Contact Information for Business Card

Dora Malcott
Brenlow, NM
505-718-2946
doramalcott@quellmail.net

```html
<!DOCTYPE html>
<html lang="en">
<head>
<meta charset="utf-8">
<title>Dora Malcott — Business Card</title>
<link rel="stylesheet" href="https://fonts.googleapis.com/css2?family=Advent+Pro:wght@400&family=Marcellus&display=swap">
<style>
  :root {
    --backdrop: #e9e6e1;
    --card-dark: #2a2828;
    --cream: #ecebd9;
    --gold: #f0b10f;
    --ink: #1f1d1c;
    --white: #ffffff;
  }
  * { box-sizing: border-box; margin: 0; padding: 0; }
  html, body {
    width: 1200px; height: 504px; overflow: hidden;
    background: var(--backdrop);
  }
  .stage {
    position: relative; width: 1200px; height: 504px;
  }
  .card {
    position: absolute; top: 97px;
    width: 540px; height: 310px;
    box-shadow: 0 6px 18px rgba(0,0,0,0.25);
  }
  .card-front { left: 40px; background: var(--card-dark); }
  .card-back { left: 620px; overflow: hidden; }

  .name-badge {
    position: absolute; left: 50px; top: 83px;
    width: 144px; height: 144px; border-radius: 50%;
    background: var(--cream);
    border: 3px solid var(--gold);
    box-shadow: 0 0 0 4px var(--cream) inset;
    display: flex; align-items: center; justify-content: center;
    text-align: center;
  }
  .name-badge .name {
    font-family: "Advent Pro", sans-serif;
    font-size: 36px; line-height: 36px; color: var(--ink);
    letter-spacing: 0.5px;
  }

  .contact-panel {
    position: absolute; left: 272px; top: 82px;
    width: 248px; height: 186px;
    background: var(--cream);
    font-family: "Marcellus", serif; color: var(--ink);
    padding: 16px 14px 0 14px;
  }
  .contact-row {
    display: flex; align-items: center; gap: 6px;
    font-size: 13.5px; line-height: 20px;
    white-space: nowrap;
  }
  .contact-row svg { flex: none; width: 13px; height: 13px; }
  .divider {
    border-top: 2px dotted var(--gold);
    margin: 10px 0;
  }
  .place-row { font-size: 14px; padding: 4px 0; }
  .place-row svg { width: 12px; height: 16px; }
  .tagline {
    position: absolute; left: 10px; right: 10px; bottom: 10px;
    height: 40px; background: var(--gold);
    color: var(--white); font-size: 14px;
    display: flex; align-items: center; padding-left: 12px;
  }

  .photo {
    width: 100%; height: 100%;
    background:
      radial-gradient(ellipse at 30% 70%, #e9e4da 0%, rgba(233,228,218,0) 35%),
      radial-gradient(ellipse at 75% 75%, #c9a76a 0%, rgba(201,167,106,0) 45%),
      linear-gradient(160deg, #a9b08a 0%, #8d7a5a 40%, #a08060 70%, #7c6444 100%);
  }
</style>
</head>
<body>
<main class="stage">
  <section class="card card-front">
    <div class="name-badge">
      <div class="name">Dora<br>Malcott</div>
    </div>
    <div class="contact-panel">
      <div class="contact-row">
        <svg viewBox="0 0 16 16" aria-hidden="true"><circle cx="8" cy="8" r="7" fill="none" stroke="#1f1d1c" stroke-width="1.5"/><path d="M5.5 4.5c.6-.4 1.2-.3 1.4.3l.5 1.3c.1.4 0 .7-.4 1l-.5.4c.4.9 1 1.5 1.9 1.9l.4-.5c.3-.4.6-.5 1-.4l1.3.5c.6.2.7.8.3 1.4-.6.8-1.6 1-2.6.5C7 10 6 9 5.3 7.3c-.5-1-.3-2 .2-2.8z" fill="#1f1d1c"/></svg>
        <span>505-718-2946</span>
      </div>
      <div class="contact-row">
        <svg viewBox="0 0 16 16" aria-hidden="true"><rect x="1" y="3.5" width="14" height="9.5" rx="1" fill="#1f1d1c"/><path d="M2 4.5l6 4.5 6-4.5" fill="none" stroke="#ecebd9" stroke-width="1.3"/></svg>
        <span>doramalcott@quellmail.net</span>
      </div>
      <div class="divider"></div>
      <div class="contact-row place-row">
        <svg viewBox="0 0 12 16" aria-hidden="true"><path d="M6 0.5C3 0.5 0.8 2.7 0.8 5.6 0.8 9.3 6 15.5 6 15.5s5.2-6.2 5.2-9.9C11.2 2.7 9 0.5 6 0.5z" fill="#1f1d1c"/><circle cx="6" cy="5.6" r="2" fill="#ecebd9"/></svg>
        <span>Brenlow, NM</span>
      </div>
      <div class="divider"></div>
      <div class="tagline">Animal Lover &amp; Care Taker</div>
    </div>
  </section>

  <section class="card card-back">
    <div class="photo" role="img" aria-label="Photograph of two people crouching beside resting cheetahs in a sunny enclosure with rocks and a fence"></div>
  </section>
</main>
</body>
</html>
```